business card for a massage therapy practice named 'Cedar and Willow Massage Studio'

I really need a trendy, yet easy on the eyes business card to complement my logo. Ideally with some gold or rose gold foil work.

My uploaded file of the logo I have in horizontal but I have a vertical version as well. Another color that is used in the website is a blush pink here and there. I'd like to see some trendy tropical leaves in the design.

```html
<!DOCTYPE html>
<html lang="en">
<head>
<meta charset="utf-8">
<title>Cedar and Willow Massage Studio – Business Card</title>
<link rel="stylesheet" href="https://fonts.googleapis.com/css2?family=Open+Sans:wght@400;600&display=swap">
<style>
  :root {
    --backdrop: #8f5a32;
    --kraft-light: #dcb88f;
    --kraft-mid: #c99e6f;
    --kraft-dark: #b5865a;
    --ink: #1b1410;
  }
  * { margin: 0; padding: 0; box-sizing: border-box; }
  html, body {
    width: 1200px;
    height: 900px;
    overflow: hidden;
  }
  body {
    position: relative;
    background: var(--backdrop);
    font-family: "Open Sans", Arial, sans-serif;
    color: var(--ink);
  }
  .card {
    position: absolute;
    left: 329px;
    width: 557px;
    height: 343px;
    background: linear-gradient(160deg, var(--kraft-light) 0%, var(--kraft-mid) 45%, var(--kraft-dark) 100%);
  }
  .card--back { top: 90px; }
  .card--front { top: 469px; }

  .contact {
    position: absolute;
    left: 0;
    right: 0;
    top: 86px;
    text-align: center;
  }
  .contact__name {
    font-size: 19px;
    font-weight: 600;
    letter-spacing: 0.5px;
    line-height: 24px;
  }
  .contact__role,
  .contact__line {
    font-size: 16px;
    font-weight: 400;
    line-height: 20px;
  }
  .contact__rule {
    width: 158px;
    height: 1px;
    background: var(--ink);
    margin: 8px auto 10px;
  }

  .brand {
    position: absolute;
    left: 0;
    right: 0;
    top: 120px;
    display: flex;
    align-items: center;
    justify-content: center;
    gap: 22px;
  }
  .brand__mark {
    width: 40px;
    height: 40px;
    border-radius: 50%;
    background: var(--ink);
    flex: none;
  }
  .brand__name {
    font-size: 30px;
    font-weight: 600;
    line-height: 38px;
    color: var(--ink);
  }
  .brand__name span { display: block; }
</style>
</head>
<body>
  <section class="card card--back" aria-label="Card back with contact details">
    <div class="contact">
      <p class="contact__name">MARISOL VEGA</p>
      <p class="contact__role">Massage Theraphist</p>
      <div class="contact__rule"></div>
      <p class="contact__line">2417 J St. suite 210</p>
      <p class="contact__line">Sacramento, CA 95816</p>
      <div class="contact__rule"></div>
      <p class="contact__line">(916) 555-0148</p>
      <p class="contact__line">cedarandwillow@gmail.com</p>
    </div>
  </section>

  <section class="card card--front" aria-label="Card front with studio name">
    <div class="brand">
      <div class="brand__mark"></div>
      <p class="brand__name"><span>Cedar and Willow</span><span>Massage Studio</span></p>
    </div>
  </section>
</body>
</html>
```